BRIGHT RIVER POWER.

I'd like my business logo.
contact name: Dennis Halvorsen
phone:0438759164
email: info@brightriverpower.net.au
website: www.brightriverpower.net.au

services:
solar
battery storage
LED lighting
energy saving solutions
general electrical
I'd like the design to look professional

Target Market(s)

Everyone

Industry/Entity Type

Business

Contact Information for Business Card

as described above

Requirements
Must have
• Id like the colours and the design to work well with my logo.

```html
<!DOCTYPE html>
<html lang="en">
<head>
<meta charset="utf-8">
<title>Bright River Power – Business Card</title>
<link href="https://fonts.googleapis.com/css2?family=Source+Sans+3:wght@400;600;700&display=swap" rel="stylesheet">
<style>
  :root {
    --backdrop: #ecedea;
    --paper: #ffffff;
    --green-band: #5cb87e;
    --green-deep: #4aa640;
    --green-brand: #5db548;
    --orange: #f5a01a;
    --orange-deep: #f18a12;
    --ink: #4a4a4a;
  }
  * { margin: 0; padding: 0; box-sizing: border-box; }
  html, body { width: 1200px; height: 900px; overflow: hidden; }
  body {
    background: var(--backdrop);
    font-family: "Source Sans 3", "Myriad Pro", sans-serif;
    position: relative;
  }
  .card {
    position: absolute;
    background: var(--paper);
    overflow: hidden;
    box-shadow: 0 6px 18px rgba(0,0,0,.18);
  }
  .card-front { left: 237px; top: 60px; width: 556px; height: 345px; }
  .card-back  { left: 457px; top: 518px; width: 560px; height: 344px; }
  .card-art { position: absolute; inset: 0; }

  .brand {
    position: absolute;
    color: var(--green-brand);
    font-weight: 700;
    line-height: 1;
    letter-spacing: .5px;
    display: flex;
    align-items: center;
    gap: 12px;
  }
  .brand-dot {
    width: 14px; height: 14px; border-radius: 50%;
    background: var(--green-brand);
    flex: none;
  }
  .card-front .brand { left: 36px; top: 52px; font-size: 27px; }
  .card-back .brand { left: 0; right: 0; top: 108px; justify-content: center; font-size: 34px; }

  .holder-name {
    position: absolute; left: 35px; top: 176px;
    color: var(--orange); font-weight: 700; font-size: 20px;
  }
  .contact-list {
    position: absolute; left: 35px; top: 230px;
    list-style: none; color: var(--paper); font-size: 15.5px;
  }
  .contact-list li { display: flex; align-items: center; height: 20.5px; }
  .contact-icon { width: 11px; height: 11px; margin-right: 10px; flex: none; }

  .services-title {
    position: absolute; left: 0; right: 0; top: 212px;
    text-align: center; color: var(--orange); font-weight: 700; font-size: 17px;
  }
  .services-list {
    position: absolute; left: 0; right: 0; top: 250px;
    text-align: center; color: var(--ink); font-size: 16px; line-height: 20px;
  }
</style>
</head>
<body>
  <section class="card card-front">
    <svg class="card-art" width="556" height="345" viewBox="0 0 556 345">
      <defs>
        <linearGradient id="emblemFill" x1="0" y1="0" x2="1" y2="1">
          <stop offset="0" stop-color="#f39a18"/>
          <stop offset=".5" stop-color="#6cc08a"/>
          <stop offset="1" stop-color="#8cc63e"/>
        </linearGradient>
      </defs>
      <rect class="band-top" width="556" height="147" fill="var(--paper)"/>
      <rect class="band-green" y="147" width="556" height="198" fill="var(--green-band)"/>
      <polygon class="band-diagonal" points="190,345 556,345 556,205" fill="var(--green-deep)"/>
      <circle class="emblem-ring" cx="500" cy="170" r="148" fill="var(--green-deep)"/>
      <circle class="emblem-gap" cx="500" cy="170" r="138" fill="none" stroke="var(--paper)" stroke-width="3"/>
      <circle class="emblem-art" cx="500" cy="170" r="133" fill="url(#emblemFill)"
              role="img" aria-label="Decorative sun and leaf flame artwork in orange and green"/>
    </svg>

    <div class="brand"><span class="brand-dot"></span>BRIGHT RIVER POWER</div>
    <div class="holder-name">Dennis Halvorsen</div>
    <ul class="contact-list">
      <li>
        <svg class="contact-icon" viewBox="0 0 12 12" aria-hidden="true"><path d="M2.5 1 L4.5 1 L5.2 3.5 L4 4.6 Q5 7 7.4 8 L8.5 6.8 L11 7.5 L11 9.5 Q11 11 9.5 11 Q1 10.5 1 2.5 Q1 1 2.5 1Z" fill="var(--orange)"/></svg>
        0438759164
      </li>
      <li>
        <svg class="contact-icon" viewBox="0 0 12 12" aria-hidden="true"><rect x="1" y="2.5" width="10" height="7" fill="var(--orange)"/><path d="M1 2.5 L6 6.5 L11 2.5" fill="none" stroke="var(--green-band)" stroke-width="1"/></svg>
        info@brightriverpower.net.au
      </li>
      <li>
        <svg class="contact-icon" viewBox="0 0 12 12" aria-hidden="true"><circle cx="6" cy="6" r="5.2" fill="var(--orange)"/><path d="M1 6 H11 M6 1 Q3 6 6 11 M6 1 Q9 6 6 11" fill="none" stroke="var(--green-band)" stroke-width=".8"/></svg>
        www.brightriverpower.net.au
      </li>
    </ul>
  </section>

  <section class="card card-back">
    <div class="brand"><span class="brand-dot"></span>BRIGHT RIVER POWER</div>
    <h2 class="services-title">WHAT I DO</h2>
    <p class="services-list">Solar | Battery Storage<br>LED Lighting | Energy Saving Solutions</p>
  </section>
</body>
</html>
```